Personal Injury Lawyer Billboard

I would like a design created featuring the image of the lawyer centered in the middle of the design.
To the left of the lawyer's image it should read "INJURED?"
To the right of the lawyer's image, it should read "CALL DEAN!"
Under Call Dean, include the phone number 318-555-0187.
At the bottom of the design include the lawyers information "Dean Marlowe Accident & Injury Lawyers"
PLEASE REMOVED THE BACKGROUND IMAGERY OF THE PHOTO SUBMITTED. Also, the colors for this design should match the colors shown in the logo (navy, white and relective soft gold). Please use those color combinations in ways that best stand out.

```html
<!DOCTYPE html>
<html lang="en">
<head>
<meta charset="utf-8">
<title>Dean Marlowe Accident &amp; Injury Lawyers – Billboard</title>
<link href="https://fonts.googleapis.com/css2?family=Bebas+Neue&display=swap" rel="stylesheet">
<style>
  :root {
    --navy: #0b1d45;
    --white: #ffffff;
    --gold: #d6b44f;
    --gold-deep: #e0a81e;
    --ink: #0a0a0a;
    --stage: #d4d2d3;
  }
  * { margin: 0; padding: 0; box-sizing: border-box; }
  html, body {
    width: 1200px; height: 464px; overflow: hidden;
    background: var(--stage);
  }
  .billboard {
    position: absolute; left: 54px; top: 73px;
    width: 1092px; height: 318px;
    background: var(--navy);
    overflow: hidden;
    box-shadow: 0 3px 8px rgba(0,0,0,.35);
    font-family: "Bebas Neue", "Oswald", sans-serif;
  }
  .billboard p, .billboard h1 { position: absolute; line-height: 1; white-space: nowrap; font-weight: 400; }
  .billboard__shapes { position: absolute; inset: 0; }
  .headline {
    left: 23px; top: 21px;
    color: var(--white); font-size: 152px;
  }
  .firm-name {
    left: 32px; top: 181px;
    color: var(--white); font-size: 68px; letter-spacing: .5px;
  }
  .firm-tagline {
    left: 32px; top: 250px;
    color: var(--white); font-size: 36px;
  }
  .portrait {
    position: absolute; left: 434px; top: 31px;
    width: 264px; height: 287px;
    background: linear-gradient(180deg, #8a6a55 0%, #6b5043 40%, #1b2a5a 52%, #152452 100%);
    clip-path: polygon(62px 30px, 82px 0, 140px 0, 160px 30px, 160px 128px, 200px 150px, 232px 170px, 264px 250px, 264px 287px, 0 287px, 8px 200px, 40px 150px, 62px 135px);
  }
  .cta {
    left: 680px; top: 24px;
    color: var(--gold); font-size: 106px;
  }
  .phone {
    left: 680px; top: 121px;
    color: var(--ink); font-size: 90px;
  }
  .footer-name {
    left: 711px; top: 261px;
    color: var(--white); font-size: 25px; letter-spacing: .3px;
  }
</style>
</head>
<body>
  <div class="billboard">
    <svg class="billboard__shapes" width="1092" height="318" viewBox="0 0 1092 318" aria-hidden="true">
      <polygon points="519,0 533,0 560,60 546,60" fill="var(--gold-deep)"/>
      <polygon points="533,0 1092,0 1092,233 640,233" fill="var(--white)"/>
    </svg>

    <h1 class="headline">INJURED?</h1>

    <p class="firm-name">DEAN MARLOWE</p>
    <p class="firm-tagline">ACCIDENT &amp; INJURY LAWYERS</p>

    <div class="portrait" role="img" aria-label="Cut-out photo of the lawyer in a navy suit and green tie, raising a fist"></div>

    <p class="cta">CALL DEAN!</p>
    <p class="phone">318-555-0187</p>

    <p class="footer-name">DEAN MARLOWE ACCIDENT &amp; INJURY LAWYERS</p>
  </div>
</body>
</html>
```